Business Card design which attached logo. Company is called Crestline Shield and main colours are Orange & Black.

Company specialises in Paint Protection and Detailing for supercars.

Details needed on business card:

Sales

Address: Unit 14, 517 Hadley Road, Fernvale Heights, NSW 2200

Phone: 02 6194 2738

website: www.crestlineshield.com.au

Email: sales@crestlineshield.com.au

```html
<!DOCTYPE html>
<html lang="en">
<head>
<meta charset="utf-8">
<title>Crestline Shield – Business Card</title>
<link rel="stylesheet" href="https://fonts.googleapis.com/css2?family=Montserrat:wght@300;400;500&family=Open+Sans:wght@400&display=swap">
<style>
  :root {
    --backdrop: #6e6e6e;
    --card: #0b0b0b;
    --orange: #e2491c;
    --white: #f2f2f2;
    --grey: #bdbdbd;
  }
  * { margin: 0; padding: 0; box-sizing: border-box; }
  html, body { width: 1200px; height: 857px; overflow: hidden; }
  body {
    background: var(--backdrop);
    font-family: "Montserrat", sans-serif;
    display: flex;
    align-items: center;
    justify-content: center;
    gap: 50px;
  }
  .card {
    width: 520px;
    height: 318px;
    background: var(--card);
    position: relative;
    box-shadow: 0 10px 28px rgba(0,0,0,.35);
  }
  /* front */
  .card-front .brand-name {
    position: absolute;
    left: 0; right: 0; top: 120px;
    text-align: center;
    color: var(--orange);
    font-weight: 300;
    font-size: 30px;
    letter-spacing: 1px;
    text-transform: uppercase;
  }
  .card-front .website {
    position: absolute;
    left: 0; right: 0; bottom: 50px;
    text-align: center;
    font-family: "Open Sans", sans-serif;
    font-size: 14px;
    color: var(--white);
    letter-spacing: .3px;
  }
  .accent { color: var(--orange); }

  /* back */
  .card-back .brand-name {
    position: absolute;
    left: 30px; top: 160px; width: 220px;
    text-align: center;
    color: var(--orange);
    font-weight: 300;
    font-size: 19px;
    text-transform: uppercase;
  }
  .card-back .divider {
    position: absolute;
    left: 262px; top: 70px;
    width: 2px; height: 140px;
    background: var(--orange);
  }
  .contact-block {
    position: absolute;
    left: 284px; top: 66px;
  }
  .contact-block .title {
    color: var(--orange);
    font-size: 20px;
    font-weight: 400;
    text-transform: uppercase;
    line-height: 1.1;
  }
  .contact-block .role {
    color: var(--grey);
    font-size: 15px;
    font-weight: 400;
    margin-bottom: 16px;
  }
  .contact-list { list-style: none; }
  .contact-list li {
    display: flex;
    align-items: center;
    gap: 7px;
    font-family: "Open Sans", sans-serif;
    color: var(--white);
    font-size: 12.5px;
    line-height: 20px;
  }
  .contact-list svg { width: 11px; height: 11px; flex: none; }
  .card-back .address {
    position: absolute;
    left: 30px; bottom: 32px;
    font-family: "Open Sans", sans-serif;
    font-size: 12.5px;
    color: var(--white);
  }
</style>
</head>
<body>
  <section class="card card-front">
    <div class="brand-name">Crestline Shield</div>
    <div class="website">www.<span class="accent">crestlineshield</span>.com.au</div>
  </section>

  <section class="card card-back">
    <div class="brand-name">Crestline Shield</div>
    <div class="divider"></div>
    <div class="contact-block">
      <div class="title">Crestline Shield</div>
      <div class="role">Founder &amp; CEO</div>
      <ul class="contact-list">
        <li>
          <svg viewBox="0 0 12 12" aria-hidden="true"><rect x="3" y="0.8" width="6" height="10.4" rx="1.2" fill="none" stroke="var(--orange)" stroke-width="1.2"/></svg>
          02 6194 2738
        </li>
        <li>
          <svg viewBox="0 0 12 12" aria-hidden="true"><rect x="0.8" y="2.5" width="10.4" height="7.5" fill="var(--orange)"/><path d="M0.8 2.5 L6 6.8 L11.2 2.5" fill="none" stroke="var(--card)" stroke-width="1"/></svg>
          sales@crestlineshield.com.au
        </li>
        <li>
          <svg viewBox="0 0 12 12" aria-hidden="true"><circle cx="6" cy="6" r="5" fill="none" stroke="var(--orange)" stroke-width="1.2"/><path d="M1 6 H11 M6 1 C3 4 3 8 6 11 M6 1 C9 4 9 8 6 11" fill="none" stroke="var(--orange)" stroke-width="0.9"/></svg>
          www.crestlineshield.com.au
        </li>
      </ul>
    </div>
    <div class="address"><span class="accent">Address:</span> Unit 14, 517 Hadley Road, Fernvale Heights, NSW 2200</div>
  </section>
</body>
</html>
```